Sales presentation introduction for Finance and Tech firms

Our business is two fold - 1) recruitment 2) consultancy. We would like a one or two page template that we can use to send to potential clients. The template will ideally be the same for the recruitment and consultancy side. We need to be able to edit the template to enter text.

I have attached our logo so you can see what we currently use on Corvella.

Sector is financial services and technology. We do not intent to have lots of text but the layout/images/designs to be used should cover some of page in a way that it takes up some space to avoid having to write lot of text.

Open to colour suggestions.

Please look at the attached word doc to see the text I would like for the two presentations.

Happy to answer questions.

Target Market(s)

Directors

Industry/Entity Type

Finance and tech companies

Colors
0094D4
00A9DD
6FCCEA
C7EBF8
E9F6FB

Requirements
Must have
• Editable text

```html
<!DOCTYPE html>
<html lang="en">
<head>
<meta charset="utf-8">
<title>Altivo – Consultancy Flyer</title>
<link rel="stylesheet" href="https://fonts.googleapis.com/css2?family=Roboto:wght@300;400;500;700&family=Roboto+Condensed:wght@300;400;700&family=Montserrat:wght@400&display=swap">
<style>
  :root{
    --navy:#1c3a6b;
    --navy-deep:#13284d;
    --band:#2b3a66;
    --blue:#1565c0;
    --blue-mid:#1976d2;
    --sky:#6cc0ee;
    --heading:#1d5aa8;
    --ink:#222;
    --grey-logo:#7d7d7d;
    --canvas:#eef2f6;
    --white:#fff;
  }
  *{margin:0;padding:0;box-sizing:border-box}
  html,body{width:1200px;height:2691px;overflow:hidden}
  body{background:var(--canvas);position:relative;font-family:'Roboto',sans-serif;color:var(--ink)}
  .page{position:absolute;background:var(--white);overflow:hidden}
  .page--consultancy{left:118px;top:162px;width:904px;height:1171px}
  .page--services{left:149px;top:1432px;width:873px;height:1131px}
  .abs{position:absolute}
  svg.abs{display:block}

  .brand{position:absolute;display:flex;align-items:center;gap:14px;font-family:'Roboto',sans-serif;font-weight:300;color:var(--grey-logo);letter-spacing:1px}
  .brand__square{background:var(--blue);display:block}

  .hero-claim{position:absolute;right:213px;top:138px;text-align:right;color:var(--white);font-family:'Roboto Condensed',sans-serif;line-height:1}
  .hero-claim span{display:block;font-size:31px;font-weight:400;margin-bottom:7px}
  .hero-claim small{font-size:24px}
  .hero-claim strong{display:block;font-size:46px;font-weight:700;margin-top:8px}

  .tagline{position:absolute;left:55px;top:338px;color:var(--white);font-family:'Roboto Condensed',sans-serif;font-size:23px;line-height:30px;font-weight:300}

  .intro-title{position:absolute;left:50px;top:484px;font-size:32px;font-weight:700;color:#222}
  .intro-copy{position:absolute;left:52px;top:527px;width:813px;font-size:16.6px;line-height:26.6px;text-align:justify;color:#222}

  .service-list{position:absolute;left:62px;top:730px;list-style:none;width:420px}
  .service-list li{position:relative;height:29.6px;padding-left:41px;font-size:17px;font-weight:500;color:var(--heading);line-height:26px}
  .service-list li::after{content:"";position:absolute;left:26px;right:-10px;bottom:2px;height:1px;background:linear-gradient(90deg,#8a9bb5,rgba(138,155,181,0))}
  .service-list svg{position:absolute;left:0;top:5px}

  .phone{position:absolute;display:flex;align-items:center;gap:14px;color:var(--white);font-family:'Roboto',sans-serif;font-weight:500;font-size:38px}
  .address{position:absolute;color:var(--white);font-family:'Montserrat',sans-serif;font-size:20px}
  .contact{position:absolute;color:var(--white);font-family:'Montserrat',sans-serif;font-size:14.5px;line-height:16px}

  .hero-titles{position:absolute;color:var(--white);line-height:1}
  .hero-titles .t-light{position:absolute;white-space:nowrap;font-weight:300}
  .hero-titles .t-bold{position:absolute;white-space:nowrap;font-weight:700}

  .service{position:absolute}
  .service h2{font-size:31px;font-weight:700;color:var(--heading);margin-bottom:22px;line-height:36px}
  .service p{font-size:16.4px;line-height:25.7px;text-align:justify;color:#222}
</style>
</head>
<body>

<!-- Page one: consultancy introduction -->
<section class="page page--consultancy">
  <svg class="abs" style="left:0;top:0" width="904" height="460" role="img" aria-label="Photo of a businessman pointing at a rising arrow over bar graphs, dark blue tones">
    <defs>
      <linearGradient id="heroPhoto" x1="0" y1="0" x2="1" y2="1">
        <stop offset="0" stop-color="#0f1d36"/>
        <stop offset=".55" stop-color="#3b5a84"/>
        <stop offset="1" stop-color="#0c1628"/>
      </linearGradient>
    </defs>
    <polygon points="295,0 904,0 904,438 577,438" fill="url(#heroPhoto)"/>
  </svg>
  <svg class="abs" style="left:0;top:0" width="904" height="460" aria-hidden="true">
    <polygon points="90,438 400,150 430,200 250,438" fill="var(--sky)"/>
    <polygon points="250,438 430,200 560,438" fill="var(--blue-mid)"/>
    <polygon points="295,0 340,0 600,438 555,438" fill="var(--blue)"/>
    <polygon points="0,327 680,327 742,415 0,415" fill="var(--band)" opacity=".92"/>
    <rect x="0" y="443" width="904" height="17" fill="var(--sky)"/>
  </svg>

  <div class="brand" style="left:62px;top:168px;font-size:50px">
    <i class="brand__square" style="width:20px;height:20px"></i>ALTIVO
  </div>

  <div class="hero-claim">
    <span>ALTIVO WILL</span>
    <span>ENSURE <small>YOU ARE</small></span>
    <span>PREPARED <small>FOR</small></span>
    <strong>GROWTH.</strong>
  </div>

  <p class="tagline">A partner who brings new and innovative ideas to the table,<br>through extensive industry experience and knowledge.</p>

  <h1 class="intro-title">Altivo Consultancy</h1>
  <div class="intro-copy">
    <p>Altivo E2E is a bespoke consultancy firm that specialises in buy side investment.&nbsp; Through an industry based consultative approach we assist our clients in preparing for, and facilitating, long term growth.&nbsp; Working closely with our clients we combine innovative thinking and breakthrough technologies to accelerate progress and, together, achieve enduring results.</p>
    <p>Experienced in successfully delivering change for global organisations as well as assisting smaller firms during their growth phase.&nbsp; Altivo will work with you create a workable model and ensure successful delivery of the project.</p>
  </div>

  <ul class="service-list">
    <li><svg width="22" height="18" viewBox="0 0 22 18"><path d="M4 3l7 6-7 6M11 3l7 6-7 6" fill="none" stroke="var(--blue)" stroke-width="2.4"/></svg>Order Management and Trading</li>
    <li><svg width="22" height="18" viewBox="0 0 22 18"><path d="M4 3l7 6-7 6M11 3l7 6-7 6" fill="none" stroke="var(--blue)" stroke-width="2.4"/></svg>Investment and Research</li>
    <li><svg width="22" height="18" viewBox="0 0 22 18"><path d="M4 3l7 6-7 6M11 3l7 6-7 6" fill="none" stroke="var(--blue)" stroke-width="2.4"/></svg>Static, Pricing and Benchmark Data</li>
    <li><svg width="22" height="18" viewBox="0 0 22 18"><path d="M4 3l7 6-7 6M11 3l7 6-7 6" fill="none" stroke="var(--blue)" stroke-width="2.4"/></svg>CRM/ Onboarding</li>
    <li><svg width="22" height="18" viewBox="0 0 22 18"><path d="M4 3l7 6-7 6M11 3l7 6-7 6" fill="none" stroke="var(--blue)" stroke-width="2.4"/></svg>Performance, Risk and Attribution</li>
    <li><svg width="22" height="18" viewBox="0 0 22 18"><path d="M4 3l7 6-7 6M11 3l7 6-7 6" fill="none" stroke="var(--blue)" stroke-width="2.4"/></svg>Client and Regulatory Reporting</li>
    <li><svg width="22" height="18" viewBox="0 0 22 18"><path d="M4 3l7 6-7 6M11 3l7 6-7 6" fill="none" stroke="var(--blue)" stroke-width="2.4"/></svg>Compliance</li>
    <li><svg width="22" height="18" viewBox="0 0 22 18"><path d="M4 3l7 6-7 6M11 3l7 6-7 6" fill="none" stroke="var(--blue)" stroke-width="2.4"/></svg>Finance and Accounting</li>
    <li><svg width="22" height="18" viewBox="0 0 22 18"><path d="M4 3l7 6-7 6M11 3l7 6-7 6" fill="none" stroke="var(--blue)" stroke-width="2.4"/></svg>Middle and Back Office</li>
  </ul>

  <svg class="abs" style="left:441px;top:722px" width="454" height="350" role="img" aria-label="Illustration of a laptop with financial dashboards, a 3D bar chart, pie chart and printed reports">
    <defs>
      <linearGradient id="laptopArt" x1="0" y1="0" x2="0" y2="1">
        <stop offset="0" stop-color="#dfe7f1"/>
        <stop offset="1" stop-color="#f6f8fb"/>
      </linearGradient>
    </defs>
    <rect width="454" height="350" rx="10" fill="url(#laptopArt)"/>
  </svg>

  <svg class="abs" style="left:0;top:1018px" width="370" height="68" aria-hidden="true">
    <polygon points="0,0 370,0 340,68 0,68" fill="var(--navy)"/>
  </svg>
  <div class="phone" style="left:64px;top:1030px">
    <svg width="30" height="30" viewBox="0 0 24 24"><path d="M6.6 10.8a15.1 15.1 0 0 0 6.6 6.6l2.2-2.2c.3-.3.7-.4 1-.2 1.1.4 2.3.6 3.6.6.6 0 1 .4 1 1V20c0 .6-.4 1-1 1A17 17 0 0 1 3 4c0-.6.4-1 1-1h3.5c.6 0 1 .4 1 1 0 1.3.2 2.5.6 3.6.1.3 0 .7-.2 1z" fill="none" stroke="#fff" stroke-width="1.5"/><path d="M14 3a7 7 0 0 1 7 7M14 6.5a3.5 3.5 0 0 1 3.5 3.5" fill="none" stroke="#fff" stroke-width="1.5"/></svg>
    1234567890
  </div>

  <svg class="abs" style="left:0;top:1088px" width="904" height="55" aria-hidden="true">
    <polygon points="0,0 480,0 514,55 0,55" fill="var(--navy)"/>
    <polygon points="497,0 520,0 555,55 532,55" fill="#a9b8dc"/>
    <polygon points="525,0 548,0 583,55 560,55" fill="#8096c9"/>
    <polygon points="555,0 904,0 904,55 590,55" fill="var(--blue)"/>
  </svg>
  <p class="address" style="left:51px;top:1103px">48 Harbourline Avenue New York, NY 10014</p>
  <p class="contact" style="left:647px;top:1100px">info@yourwebsite.com<br>www.yourwebsite.com</p>
</section>

<!-- Page two: services overview -->
<section class="page page--services">
  <svg class="abs" style="left:0;top:0" width="873" height="405" role="img" aria-label="Photo of a businessman drawing a rising line graph over glowing financial data, light blue tones">
    <defs>
      <linearGradient id="strategyPhoto" x1="0" y1="0" x2="1" y2="1">
        <stop offset="0" stop-color="#5ea9cf"/>
        <stop offset=".5" stop-color="#3a7fab"/>
        <stop offset="1" stop-color="#1d3f66"/>
      </linearGradient>
    </defs>
    <rect width="873" height="405" fill="url(#strategyPhoto)"/>
  </svg>

  <div class="hero-titles">
    <span class="t-light" style="left:42px;top:74px;font-size:58px">Business Strategy</span>
    <span class="t-bold" style="left:97px;top:136px;font-size:56px">MANAGEMENT</span>
    <span class="t-light" style="left:56px;top:203px;font-size:35px">IT TRANSFORMATION</span>
    <span class="t-bold" style="left:89px;top:243px;font-size:31px;font-family:'Roboto Condensed',sans-serif">Organisational structure</span>
  </div>

  <article class="service" style="left:41px;top:441px;width:349px">
    <h2>Business Strategy</h2>
    <p>Altivo will help you create a business strategy tailored to your requirements.&nbsp; Ensuring each business process is defined and taken into account allows for a successful design.&nbsp; Creating and implementing an operating model that takes into account budget, resources, culture and your company’s vision.</p>
  </article>
  <article class="service" style="left:425px;top:439px;width:410px">
    <h2>Change management</h2>
    <p>Altivo works with clients to deliver bespoke change initiatives.&nbsp; Rigorous business analysis and risk management allows for successful change initiatives.&nbsp; We work with you throughout the complete process, to ensure that delivery is based on value. Transition phases are challenging aspects of change initiatives which is why our team manage all transitions and the risk they carry.</p>
  </article>
  <article class="service" style="left:41px;top:710px;width:349px">
    <h2>IT transformation</h2>
    <p>Altivo is widely experienced in a range of technologies.&nbsp; We help with the implementation of software provider or design and develop bespoke services.&nbsp; Covering front to back office the team specialises in full project lifecycle from feasibility through to implementation.</p>
  </article>
  <article class="service" style="left:425px;top:708px;width:410px">
    <h2>Organisational structure</h2>
    <p>Altivo works with clients to improve resource capability and strategic partnerships. Acting as an extension of the HR function, we analyse business processes and ensure that our clients have the ability to manage changing workforce demands.</p>
  </article>

  <div class="brand" style="left:51px;top:948px;font-size:40px">
    <i class="brand__square" style="width:16px;height:16px"></i>ALTIVO
  </div>

  <svg class="abs" style="left:535px;top:992px" width="338" height="64" aria-hidden="true">
    <polygon points="0,0 338,0 338,64 30,64" fill="var(--navy)"/>
  </svg>
  <div class="phone" style="left:598px;top:1003px">
    <svg width="30" height="30" viewBox="0 0 24 24"><path d="M6.6 10.8a15.1 15.1 0 0 0 6.6 6.6l2.2-2.2c.3-.3.7-.4 1-.2 1.1.4 2.3.6 3.6.6.6 0 1 .4 1 1V20c0 .6-.4 1-1 1A17 17 0 0 1 3 4c0-.6.4-1 1-1h3.5c.6 0 1 .4 1 1 0 1.3.2 2.5.6 3.6.1.3 0 .7-.2 1z" fill="none" stroke="#fff" stroke-width="1.5"/><path d="M14 3a7 7 0 0 1 7 7M14 6.5a3.5 3.5 0 0 1 3.5 3.5" fill="none" stroke="#fff" stroke-width="1.5"/></svg>
    1234567890
  </div>

  <svg class="abs" style="left:0;top:1056px" width="873" height="49" aria-hidden="true">
    <polygon points="0,0 464,0 493,49 0,49" fill="var(--navy)"/>
    <polygon points="478,0 500,0 530,49 508,49" fill="#a9b8dc"/>
    <polygon points="506,0 528,0 558,49 536,49" fill="#8096c9"/>
    <polygon points="536,0 873,0 873,49 566,49" fill="var(--blue)"/>
  </svg>
  <p class="address" style="left:49px;top:1068px">48 Harbourline Avenue New York, NY 10014</p>
  <p class="contact" style="left:624px;top:1064px">info@yourwebsite.com<br>www.yourwebsite.com</p>
</section>

</body>
</html>
```